Specialised investor in e-mobility and energy wants business card design

We need a business card design that fits our existing corporate design. <The look and feel must be 'sharp'/'clean', dynamic, communicate momentum, professionalism etc (as one would imagine from a firm in the financial sector). We like the idea of a reverse-side of the card that includes the logo, and the name and contact details on the other. We expect the deliverable to be whatever format might be required to be able to get cards printed directly by a service such as kelmo press. Our website is www.zub.capital

```html
<!DOCTYPE html>
<html lang="en">
<head>
<meta charset="utf-8">
<title>Zub Capital – Business Card</title>
<link href="https://fonts.googleapis.com/css2?family=Montserrat:wght@400;500;700&display=swap" rel="stylesheet">
<style>
  :root {
    --green-dark: #2f4d22;
    --green-light: #86b24a;
    --ink: #2e2e2e;
    --paper: #ffffff;
    --backdrop: #e4e4e1;
  }
  * { box-sizing: border-box; margin: 0; padding: 0; }
  html, body {
    width: 1200px; height: 801px; overflow: hidden;
    background: var(--backdrop);
    font-family: "Montserrat", sans-serif;
  }
  .card {
    position: absolute; top: 245px;
    width: 540px; height: 310px;
    background: var(--paper);
    border-bottom: 3px solid var(--green-light);
    overflow: hidden;
  }
  .card--front { left: 40px; }
  .card--back { left: 620px; }

  .card__band { position: absolute; inset: 0; width: 540px; height: 310px; }

  .wordmark {
    position: absolute; display: flex; align-items: center; gap: 10px;
    color: var(--green-dark); font-weight: 500; white-space: nowrap;
  }
  .wordmark__dot { border-radius: 50%; background: var(--green-light); flex: none; }
  .card--front .wordmark { left: 38px; top: 136px; font-size: 32px; }
  .card--front .wordmark__dot { width: 14px; height: 14px; }
  .card--back .wordmark { left: 0; right: 0; top: 112px; justify-content: center; font-size: 62px; gap: 16px; }
  .card--back .wordmark__dot { width: 24px; height: 24px; }

  .divider {
    position: absolute; left: 250px; top: 58px;
    width: 1px; height: 196px; background: var(--green-light);
  }
  .contact { position: absolute; left: 272px; top: 52px; color: var(--ink); }
  .contact__name { color: var(--green-light); font-weight: 700; font-size: 19px; letter-spacing: .5px; }
  .contact__role { font-size: 13px; margin-top: 2px; }
  .contact__list { list-style: none; margin-top: 16px; font-size: 12.5px; line-height: 19px; }
  .contact__list li { display: flex; align-items: center; gap: 8px; }
  .contact__list svg { width: 12px; height: 12px; fill: var(--green-light); flex: none; }
  .contact__company { color: var(--green-light); font-size: 13px; margin-top: 16px; }
  .contact__city { font-size: 13px; margin-top: 2px; }
</style>
</head>
<body>
  <section class="card card--front">
    <svg class="card__band" viewBox="0 0 540 310" aria-hidden="true">
      <path d="M540 120 L540 310 L405 310 C455 240 495 175 540 120Z" fill="var(--green-light)"/>
      <path d="M372 310 C420 225 470 160 532 100 C478 170 432 235 398 310Z" fill="var(--green-dark)"/>
    </svg>

    <div class="wordmark"><span class="wordmark__dot"></span>zub capital</div>
    <div class="divider"></div>

    <div class="contact">
      <p class="contact__name">ELIAS BRANDT</p>
      <p class="contact__role">Managing Director</p>
      <ul class="contact__list">
        <li><svg viewBox="0 0 24 24"><path d="M6.6 10.8a15 15 0 0 0 6.6 6.6l2.2-2.2a1 1 0 0 1 1-.25 11.4 11.4 0 0 0 3.6.57 1 1 0 0 1 1 1V20a1 1 0 0 1-1 1A17 17 0 0 1 3 4a1 1 0 0 1 1-1h3.5a1 1 0 0 1 1 1c0 1.25.2 2.45.57 3.57a1 1 0 0 1-.25 1z"/></svg>+41 79 555 0148</li>
        <li><svg viewBox="0 0 24 24"><path d="M2 5h20v14H2z M2 5l10 8 10-8" /></svg>elias@zub.capital</li>
        <li><svg viewBox="0 0 24 24"><circle cx="12" cy="12" r="10"/></svg>www.zub.capital</li>
      </ul>
      <p class="contact__company">Zub Capital S.A.</p>
      <p class="contact__city">Lausanne, Switzerland</p>
    </div>
  </section>

  <section class="card card--back">
    <div class="wordmark"><span class="wordmark__dot"></span>zub capital</div>
  </section>
</body>
</html>
```